Cat-products company needs smart, yet endearing, business card

We need a business card design for a new, but up-and-running, business based in Honolulu, Hawaii. The business is Purrnest Nook Co. Our first product is the most environmentally-friendly cat grass kit ever seen on the planet. Future products, currently in the R&D phase, will include a variety of exciting cat scratchers. We also do consulting work to help apartment-dwellers make their home more cat-friendly and, in the future, plan on doing full, custom installs of structure to create high walkways for cats.

Target Market(s)

Middle-aged, apartment-dwelling, middle-class workers who own 1 or more cats and who dote on them.

Industry/Entity Type

Pet Care

Contact Information for Business Card

A striking, professional, yet warm and friendly design is what we're after.

Font styles to use
Serif
Sans Serif
Other font styles liked:
• Comfortaa

Colors

Designer to choose colors to be used in the design.

Requirements
Must have
• The company logo: (see attachment)
• The company name: Purrnest Nook Co
• The web address: www.purrnestnookco.com
• Email: support@purrnestnookco.com
• Phone: +1 (808) 571 6023
• Update (Fri Jun 30 3017 7:45pm Hawaii Time) I would like, is possible, uploaded picture of the cat grass kit on the back of the card with some text along the lines of: Purrnest Nook Co - Maker Of The Leafiest Feline Sprout Set Yet
Nice to have
• A cat picture, cartoon, real or silhouette that illustrates cats in action and/or relaxing; ie using the apartment space to live, play and relax in and being well-contented.
• Most of the website is done in the font: Comfortaa. It might be nice to continue using this for brand consistency.
Should not have
• Hard-to-read fonts.

```html
<!DOCTYPE html>
<html lang="en">
<head>
<meta charset="utf-8">
<title>Purrnest Nook Co — Business Card</title>
<link rel="stylesheet" href="https://fonts.googleapis.com/css2?family=Oswald:wght@400;500&family=Questrial&display=swap">
<style>
  :root {
    --backdrop: #2b2b2b;
    --card-white: #f1f1f0;
    --brand-brown: #54302a;
    --brand-gold: #f0ab00;
    --text-grey: #4a4a4a;
    --divider: #c9c9c9;
    --band-text: #f4ece6;
  }
  * { box-sizing: border-box; margin: 0; padding: 0; }
  html, body { width: 1200px; height: 960px; overflow: hidden; }
  body { background: var(--backdrop); position: relative; font-family: "Questrial", sans-serif; }

  .card { position: absolute; width: 600px; height: 342px; border-radius: 18px; overflow: hidden; }

  /* Front */
  .card-front { left: 314px; top: 114px; background: var(--card-white); }
  .brand-lockup { position: absolute; left: 60px; top: 88px; width: 200px; text-align: center; }
  .brand-dot { display: block; width: 26px; height: 26px; border-radius: 50%; background: var(--brand-gold); margin: 0 auto 12px; }
  .brand-name { font-family: "Oswald", sans-serif; font-weight: 500; font-size: 36px; line-height: 1.05; color: var(--brand-brown); text-transform: uppercase; }
  .divider { position: absolute; left: 283px; top: 80px; width: 1px; height: 165px; background: linear-gradient(var(--card-white), var(--divider) 20%, var(--divider) 80%, var(--card-white)); }
  .contact { position: absolute; left: 322px; top: 84px; color: var(--text-grey); }
  .contact-name { font-family: "Oswald", sans-serif; font-weight: 400; font-size: 24px; color: var(--brand-brown); line-height: 1.1; }
  .contact-role { font-size: 15px; color: var(--brand-gold); margin-top: 3px; }
  .contact-address { font-size: 15px; line-height: 19px; margin-top: 16px; }
  .contact-lines { list-style: none; margin-top: 10px; font-size: 15px; line-height: 19px; }
  .contact-lines li { display: flex; align-items: center; gap: 8px; }
  .contact-lines svg { width: 13px; height: 13px; fill: var(--brand-brown); }

  .footer-band { position: absolute; left: 0; top: 297px; width: 600px; height: 27px; }
  .footer-band-brown { position: absolute; left: 0; top: 0; width: 500px; height: 27px; background: var(--brand-brown); }
  .footer-band-gold { position: absolute; left: 516px; top: 0; width: 84px; height: 27px; background: var(--brand-gold); }
  .footer-url { position: absolute; left: 118px; top: 4px; font-size: 15px; letter-spacing: 2.6px; color: var(--band-text); }
  .footer-mark { position: absolute; left: 484px; top: -8px; width: 32px; height: 32px; background: var(--brand-brown); border: 2px solid var(--card-white); }

  /* Back */
  .card-back { left: 311px; top: 472px; background: var(--brand-gold); }
  .social-links { position: absolute; right: 16px; top: 19px; display: flex; gap: 2px; list-style: none; }
  .social-links li { width: 22px; height: 22px; border-radius: 50%; background: var(--brand-brown); opacity: .85; }
  .back-lockup { position: absolute; left: 0; top: 92px; width: 600px; text-align: center; }
  .back-dot { display: block; width: 70px; height: 70px; border-radius: 50%; background: var(--brand-brown); margin: 0 auto 16px; }
  .back-name { font-family: "Oswald", sans-serif; font-weight: 500; font-size: 44px; line-height: 1; color: var(--brand-brown); text-transform: uppercase; }
  .back-url { position: absolute; left: 0; top: 293px; width: 600px; text-align: center; font-size: 15px; letter-spacing: 4px; color: var(--brand-brown); }
</style>
</head>
<body>
  <section class="card card-front" aria-label="Business card front">
    <div class="brand-lockup">
      <span class="brand-dot"></span>
      <div class="brand-name">Purrnest<br>Nook Co</div>
    </div>
    <div class="divider"></div>
    <div class="contact">
      <h1 class="contact-name">MALIA KAHALE</h1>
      <p class="contact-role">CEO/FOUNDER</p>
      <p class="contact-address">4120 Kilinoe Street<br>Honolulu, Hawaii 96817</p>
      <ul class="contact-lines">
        <li><svg viewBox="0 0 24 24" aria-hidden="true"><path d="M6.6 10.8a15.1 15.1 0 0 0 6.6 6.6l2.2-2.2a1 1 0 0 1 1-.25 11.4 11.4 0 0 0 3.6.57 1 1 0 0 1 1 1V20a1 1 0 0 1-1 1A17 17 0 0 1 3 4a1 1 0 0 1 1-1h3.5a1 1 0 0 1 1 1c0 1.25.2 2.45.57 3.57a1 1 0 0 1-.25 1z"/></svg>+1 (808) 571 6023</li>
        <li><svg viewBox="0 0 24 24" aria-hidden="true"><path d="M2 5h20v14H2z M2 5l10 8 10-8" fill="var(--brand-brown)"/><path d="M3 6l9 7 9-7" fill="none" stroke="var(--card-white)" stroke-width="1.6"/></svg>support@purrnestnookco.com</li>
      </ul>
    </div>
    <div class="footer-band">
      <div class="footer-band-brown"></div>
      <div class="footer-band-gold"></div>
      <span class="footer-url">www.purrnestnookco.com</span>
      <span class="footer-mark"></span>
    </div>
  </section>

  <section class="card card-back" aria-label="Business card back">
    <ul class="social-links" aria-label="Social links">
      <li></li><li></li><li></li><li></li>
    </ul>
    <div class="back-lockup">
      <span class="back-dot"></span>
      <div class="back-name">Purrnest Nook Co</div>
    </div>
    <p class="back-url">www.purrnestnookco.com</p>
  </section>
</body>
</html>
```